Upmarket Dessert Lounge needs a Business Card Design

We are an upmarket dessert lounge needing a business card to match our image.

We want something that is simple yet beautiful, feminine, classy, sophisticated and elegant. We want it to stand out and don't mind if it is bold.

The design should include our logo and colours of red or maroon with gold highlights. We don't mind if black is used.

Marlow & Quince

Target Market(s)

For those who like to indulge or treat themselves and give in to their temptations on good quality desserts.

Industry/Entity Type

Business

Requirements
Must have
• Must include our logo and our name

Marlow & Quince

M & Q

```html
<!DOCTYPE html>
<html lang="en">
<head>
<meta charset="utf-8">
<title>Marlow &amp; Quince — Business Card</title>
<link rel="stylesheet" href="https://fonts.googleapis.com/css2?family=Libre+Baskerville:wght@400;700&family=Open+Sans:wght@400;600&display=swap">
<style>
  :root {
    --maroon: #7a1416;
    --gold: #f4d29c;
    --paper: #ffffff;
    --ink: #2e2e2e;
    --muted: #555555;
    --backdrop: #ece8e3;
  }
  * { box-sizing: border-box; margin: 0; padding: 0; }
  html, body {
    width: 1200px; height: 758px; overflow: hidden;
    background: var(--backdrop);
  }
  .sheet {
    position: relative; width: 1200px; height: 758px;
    display: flex; align-items: center; justify-content: center; gap: 60px;
  }
  .card {
    position: relative; width: 540px; height: 308px;
    background: var(--paper); border-radius: 24px; overflow: hidden;
    box-shadow: 0 10px 28px rgba(0,0,0,.18);
  }

  /* Front */
  .card__band { position: absolute; inset: 0; width: 540px; height: 308px; }
  .brand-name {
    position: absolute; left: 40px; top: 48px;
    font-family: "Libre Baskerville", Georgia, serif; font-weight: 700;
    font-size: 30px; letter-spacing: .5px; color: var(--maroon);
  }
  .holder { position: absolute; right: 40px; top: 104px; text-align: right; }
  .holder__name {
    font-family: "Libre Baskerville", Georgia, serif; font-weight: 700;
    font-size: 19px; color: var(--maroon);
  }
  .holder__title {
    font-family: "Open Sans", Arial, sans-serif; font-size: 13px; color: var(--muted);
  }
  .contact {
    position: absolute; left: 34px; top: 150px; list-style: none;
    font-family: "Open Sans", Arial, sans-serif; font-size: 13px; color: var(--ink);
  }
  .contact li { display: flex; align-items: center; gap: 7px; height: 19px; }
  .contact svg { width: 12px; height: 12px; fill: var(--ink); flex: none; }
  .address {
    position: absolute; right: 30px; top: 214px; text-align: right;
    font-family: "Open Sans", Arial, sans-serif; font-size: 13px; line-height: 19px;
    color: var(--paper);
  }

  /* Back */
  .card--back { display: flex; flex-direction: column; align-items: center; justify-content: center; }
  .monogram {
    font-family: "Libre Baskerville", Georgia, serif; font-weight: 700;
    font-size: 84px; color: var(--maroon); line-height: 1;
  }
  .web {
    margin-top: 38px;
    font-family: "Open Sans", Arial, sans-serif; font-size: 21px;
    letter-spacing: 3px; color: var(--ink);
  }
</style>
</head>
<body>
<main class="sheet">
  <article class="card card--front">
    <svg class="card__band" viewBox="0 0 540 308" aria-hidden="true">
      <path d="M0,266 C120,290 300,235 540,168 L540,308 L0,308 Z" fill="var(--maroon)"/>
      <path d="M150,272 C280,250 410,190 540,150" fill="none" stroke="var(--gold)" stroke-width="3"/>
    </svg>
    <h1 class="brand-name">Marlow &amp; Quince</h1>
    <div class="holder">
      <p class="holder__name">Your name</p>
      <p class="holder__title">Title</p>
    </div>
    <ul class="contact">
      <li><svg viewBox="0 0 12 12"><circle cx="6" cy="6" r="5.5" fill="none" stroke="currentColor"/><path d="M4 3.2l1 1.4-.6.7c.4.9 1 1.5 1.9 1.9l.7-.6 1.4 1-.7 1.2C5.9 8.6 3.4 6.1 3.2 4z"/></svg>555-201-4870</li>
      <li><svg viewBox="0 0 12 12"><rect x="3" y="0.5" width="6" height="11" rx="1"/><rect x="4" y="2" width="4" height="6" fill="#fff"/></svg>555-201-4871</li>
      <li><svg viewBox="0 0 12 12"><rect x="0.5" y="2.5" width="11" height="7"/><path d="M0.5 2.5L6 7l5.5-4.5" fill="none" stroke="#fff"/></svg>hello@marlowquince.com</li>
      <li><svg viewBox="0 0 12 12"><circle cx="6" cy="6" r="5.5"/><path d="M0.5 6h11M6 .5v11M6 .5c-3 3-3 8 0 11M6 .5c3 3 3 8 0 11" fill="none" stroke="#fff" stroke-width=".7"/></svg>www.marlowquince.com</li>
    </ul>
    <p class="address">Street Name, City Name<br>State Zip Code</p>
  </article>

  <article class="card card--back">
    <p class="monogram">M &amp; Q</p>
    <p class="web">www.marlowquince.com</p>
  </article>
</main>
</body>
</html>
```